design a construction company business card

Design business card around our logo. Card must have all the typical info: name, title, address, phone, email, business name, etc. Somewhere on the card I would like to see our motto "Built on integrity... Inspired by commitment." Consider adding a splash of bright orange to the card to complement the blues and silvers/grays in the logo. We are open to metallic inks, textures, etc. We would like to see options on both light and dark backgrounds. The font in the logo is Euro Technic Extended Regular.

```html
<!DOCTYPE html>
<html lang="en">
<head>
<meta charset="utf-8">
<title>Hartwell Contracting – Business Card</title>
<link href="https://fonts.googleapis.com/css2?family=Open+Sans:wght@400;600&family=Michroma&display=swap" rel="stylesheet">
<style>
  :root {
    --backdrop: #2b2b2d;
    --card: #1e1e20;
    --ink-white: #f4f4f4;
    --ink-silver: #8e8f93;
    --ink-muted: #45454a;
    --accent-blue: #2a57c9;
    --accent-blue-light: #1d7fd6;
    --accent-blue-deep: #27339a;
  }
  * { box-sizing: border-box; margin: 0; padding: 0; }
  html, body { width: 1200px; height: 895px; overflow: hidden; }
  body {
    background: var(--backdrop);
    font-family: "Open Sans", Arial, sans-serif;
    position: relative;
  }
  .card {
    position: absolute;
    width: 525px;
    height: 300px;
    background: var(--card);
    border-radius: 14px;
    box-shadow: 0 18px 40px rgba(0,0,0,.55);
    overflow: hidden;
  }
  /* Front */
  .card--front { left: 70px; top: 90px; }
  .brand {
    position: absolute;
    left: 0; right: 0; top: 100px;
    text-align: center;
    font-family: "Open Sans", Arial, sans-serif;
    font-weight: 600;
    font-size: 26px;
    letter-spacing: 3px;
    color: var(--ink-silver);
    text-transform: uppercase;
  }
  .motto {
    position: absolute;
    left: 0; right: 0; top: 190px;
    text-align: center;
    font-size: 14px;
    letter-spacing: .5px;
    color: var(--ink-muted);
  }
  /* Back */
  .card--back { left: 605px; top: 500px; }
  .card--back::after {
    content: "";
    position: absolute; left: 0; right: 0; bottom: 0; height: 5px;
    background: linear-gradient(90deg, var(--accent-blue-light), var(--accent-blue-deep));
  }
  .identity {
    position: absolute; left: 20px; top: 106px; width: 238px;
    text-align: right;
  }
  .identity__name {
    font-family: "Michroma", Arial, sans-serif;
    font-size: 21px; font-weight: 400;
    white-space: nowrap;
    color: var(--ink-white);
    -webkit-text-stroke: .8px var(--ink-white);
  }
  .identity__title {
    margin-top: 2px;
    font-size: 14px;
    color: var(--accent-blue);
  }
  .divider {
    position: absolute; left: 273px; top: 88px;
    width: 1.5px; height: 78px; background: var(--ink-white);
  }
  .contact {
    position: absolute; left: 292px; top: 86px;
    list-style: none;
  }
  .contact__item {
    display: flex; align-items: center; gap: 9px;
    font-size: 14px; line-height: 26px;
    color: var(--ink-white);
    white-space: nowrap;
  }
  .contact__item svg { width: 15px; height: 15px; flex: none; }
  .contact__hl { color: var(--accent-blue); }
  .address {
    position: absolute; left: 0; right: 0; bottom: 44px;
    text-align: center;
    font-size: 14px; letter-spacing: .3px;
    color: var(--ink-white);
  }
</style>
</head>
<body>

<section class="card card--front" aria-label="Card front">
  <p class="brand">Hartwell Contracting, Inc.</p>
  <p class="motto">Built on integrity... Inspired by commitment</p>
</section>

<section class="card card--back" aria-label="Card back">
  <div class="identity">
    <h1 class="identity__name">DANA MARSH</h1>
    <p class="identity__title">Founder &amp; CEO</p>
  </div>
  <div class="divider"></div>
  <ul class="contact">
    <li class="contact__item">
      <svg viewBox="0 0 16 16" fill="none" stroke="#2a57c9" stroke-width="1.4"><rect x="4" y="1" width="8" height="14" rx="1.5"/><line x1="7" y1="12.5" x2="9" y2="12.5"/></svg>
      555 014 2290
    </li>
    <li class="contact__item">
      <svg viewBox="0 0 16 16" fill="none" stroke="#2a57c9" stroke-width="1.4"><rect x="1.5" y="3.5" width="13" height="9" rx="1"/><polyline points="1.5,4 8,9 14.5,4"/></svg>
      <span>info@<span class="contact__hl">hartwellbuild</span>.com</span>
    </li>
    <li class="contact__item">
      <svg viewBox="0 0 16 16" fill="none" stroke="#2a57c9" stroke-width="1.4"><circle cx="9" cy="7" r="5"/><line x1="5.5" y1="10.5" x2="1.5" y2="14.5"/></svg>
      <span>www.<span class="contact__hl">hartwellbuild</span>.com</span>
    </li>
  </ul>
  <p class="address">48 Alder Row, Suite # B, Leeds, United Kingdom LS2 7QA</p>
</section>

</body>
</html>
```